Building company buisness cards

We are looking for a sharp modern new look for our business cards.
We are a New Zealand based company that specialises in house and land packages.
We have attached a photo of the current logo and would like to see if it can be improved somehow if needed.
We are open to any colours but we have chosen green at this stage.
Feel free to change the font and make the logo smarter looking.
Play with the colours and see what looks best.

We want a card that looks so good know one will want to throw it away!

Target Market(s)

Home buyers

Industry/Entity Type

Building

Contact Information for Business Card

Derek Tolvane
0217394062
dtolvane@quillmarkhomesteads.co.nz
quillmarkhomesteads.co.nz

Font styles to use
Serif
Sans Serif

Colors

Designer to choose colors to be used in the design.

Requirements
Must have
• Logo and company name on one side, details on the other side
Nice to have
• Color codes for the original green are HEX #4a8028, RGB(74,128,40), CMYK(42,0,69,50)
• Round corners, Raised and/or spot UV

```html
<!DOCTYPE html>
<html lang="en">
<head>
<meta charset="utf-8">
<title>Quillmark Homesteads – Business Cards</title>
<link rel="stylesheet" href="https://fonts.googleapis.com/css2?family=Open+Sans:wght@400;800&family=Lato:wght@700&display=swap">
<style>
  :root {
    --brand-green: #4a8028;
    --card-white: #ffffff;
    --backdrop: #dcdcdc;
    --rule-light: #cfd8c8;
    --rule-dark: rgba(255,255,255,0.6);
  }
  * { box-sizing: border-box; margin: 0; padding: 0; }
  html, body {
    width: 1200px; height: 900px; overflow: hidden;
    background: var(--backdrop);
    font-family: "Open Sans", Arial, sans-serif;
  }
  .card-set {
    position: relative; width: 1200px; height: 900px;
  }
  .card {
    position: absolute; top: 300px;
    width: 520px; height: 300px;
    border-radius: 26px;
    display: flex; flex-direction: column; align-items: center;
  }
  .card--front { left: 50px; background: var(--card-white); color: var(--brand-green); }
  .card--back  { left: 630px; background: var(--brand-green); color: var(--card-white); }

  /* front */
  .brand-mark {
    margin-top: 92px;
    display: flex; align-items: center; gap: 12px;
  }
  .brand-square {
    width: 22px; height: 22px; background: var(--brand-green);
  }
  .brand-name {
    font-weight: 800; font-size: 34px; line-height: 1;
    letter-spacing: -0.5px;
  }
  .front-rule {
    width: 90px; height: 1px; background: var(--rule-light);
    margin-top: 22px;
  }
  .front-web {
    margin-top: 62px; font-size: 15px;
  }

  /* back */
  .back-brand {
    margin-top: 70px;
    font-weight: 800; font-size: 30px; letter-spacing: -0.5px; line-height: 1;
  }
  .holder-name {
    margin-top: 40px;
    font-family: "Lato", Arial, sans-serif;
    font-weight: 700; font-size: 19px; letter-spacing: 0.5px;
    text-transform: uppercase;
  }
  .back-rule {
    width: 200px; height: 1px; background: var(--rule-dark);
    margin: 6px 0 8px;
  }
  .contact-list {
    list-style: none; text-align: center;
    font-size: 15px; line-height: 1.35;
  }
</style>
</head>
<body>
  <main class="card-set">
    <section class="card card--front" aria-label="Card front">
      <div class="brand-mark">
        <span class="brand-square"></span>
        <span class="brand-name">quillmark homesteads</span>
      </div>
      <div class="front-rule"></div>
      <p class="front-web">www.quillmarkhomesteads.co.nz</p>
    </section>

    <section class="card card--back" aria-label="Card back">
      <p class="back-brand">quillmark homesteads</p>
      <h1 class="holder-name">Derek Tolvane</h1>
      <div class="back-rule"></div>
      <ul class="contact-list">
        <li>0217394062</li>
        <li>dtolvane@quillmarkhomesteads.co.nz</li>
        <li>www.quillmarkhomesteads.co.nz</li>
      </ul>
    </section>
  </main>
</body>
</html>
```